Logo, Web and Mobile Designs for enterprise social media platform

All the details are in the attached document, please start reading the scope document first which explains what is this project about and the details about the needed deliverables, after that please read the UI_Requirements document which will detail what is expected regarding the coded web version since this is a coded contest, it is very important that you meet the UI requirements or suggest something else but we will need to agree first before working on the coded version

Good Luck

Target Market(s)

Enterprise Social Media

Industry/Entity Type

Media

Coding

Coded - Design and coding required

Number of Pages Required

5+ page

Font styles to use
Sans Serif

Requirements
Must have
• All the must haves are listed in the scope document so please check before you start

```html
<!DOCTYPE html>
<html lang="en">
<head>
<meta charset="utf-8">
<title>Teamora – Session Details</title>
<link href="https://fonts.googleapis.com/css2?family=Roboto:wght@400;500&family=Open+Sans:wght@400&display=swap" rel="stylesheet">
<style>
:root{
  --brand:#1b8fc4;
  --brand-dark:#0d7fb6;
  --orange:#f39c1e;
  --page:#ebebeb;
  --panel:#ffffff;
  --sidebar:#f3f3f3;
  --line:#dedede;
  --text:#555;
  --muted:#777;
  --footer:#1e8ab5;
}
*{box-sizing:border-box;margin:0;padding:0}
html,body{width:1194px;height:1200px;overflow:hidden;background:var(--page)}
body{font-family:"Roboto",sans-serif;color:var(--text)}
.stage{position:absolute;left:0;top:0;width:1400px;height:1407px;transform:scale(.852857);transform-origin:0 0}
.abs{position:absolute}

/* header */
.topbar{left:0;top:0;width:1400px;height:82px;background:#f9f9f9;border-bottom:1px solid #ddd}
.topbar .divider{top:0;width:1px;height:82px;background:#e4e4e4}
.brand{left:196px;top:18px;display:flex;align-items:center;gap:12px}
.brand-dot{width:52px;height:44px;border-radius:50%;background:var(--orange)}
.brand-name{font-size:36px;font-weight:500;color:var(--brand)}
.user{left:870px;top:22px;display:flex;align-items:center;gap:14px;font-size:19px;color:#444}
.avatar{width:40px;height:40px;border-radius:50%;background:linear-gradient(#5a5a5a,#2b2b2b)}
.badge{width:26px;height:20px;border-radius:10px;color:#fff;font-size:13px;text-align:center;line-height:20px}

/* layout */
.panel{left:115px;top:123px;width:1168px;height:1059px;background:#fafafa;border:2px solid #ddd}
.sidebar{left:0;top:0;width:323px;height:1055px;background:var(--sidebar);border-right:2px solid #ddd}
.side-main{height:65px;display:flex;align-items:center;padding-left:20px;gap:16px;font-size:18px;color:#333;border-bottom:2px solid #e6e6e6;text-transform:uppercase}
.side-list{list-style:none;margin-top:22px}
.side-list li{height:38px;display:flex;align-items:center;padding-left:22px;gap:20px;font-size:19px;color:#555;border-bottom:1px solid #e4e4e4}
.side-list li.active{color:var(--brand);text-transform:uppercase}

.card{left:478px;top:167px;width:770px;height:971px;background:var(--panel);border:1px solid #e5e5e5}
.card-head{height:58px;background:#f7f7f9;border-bottom:1px solid #e3e3e3;display:flex;align-items:center;gap:12px;padding-left:24px;font-size:18px;color:#333;text-transform:uppercase}

.label{font-size:17px;color:var(--text)}
.field{background:#fff;border:1px solid #ddd;font-family:"Open Sans",sans-serif;font-size:12px;color:#333;padding-left:20px;display:flex;align-items:center}
.file{display:flex;align-items:center;gap:8px;font-size:15px;color:#444}
.time{display:flex;border:1px solid #ddd;height:45px;font-size:17px;color:#666}
.time .hm{width:116px;display:flex;align-items:center;justify-content:center;gap:12px;border-right:1px solid #ddd}
.time .spin{width:40px;border-right:1px solid #ddd;display:flex;flex-direction:column;align-items:center;justify-content:center;gap:6px}
.time .ap{width:50px;display:flex;align-items:center;justify-content:center}
.btn{left:694px;top:953px;width:173px;height:42px;background:var(--brand-dark);color:#fff;font-size:18px;font-weight:500;display:flex;align-items:center;justify-content:center;border-radius:2px;box-shadow:0 2px 0 #0a5d86}

/* footer */
.footer{left:0;top:1234px;width:1400px;height:173px;background:var(--footer);color:#fff;text-align:center}
.social{display:flex;justify-content:center;gap:15px;margin-top:34px}
.social span{width:28px;height:28px;border-radius:5px;background:#fff}
.foot-links{margin-top:22px;font-size:17px;word-spacing:2px}
.foot-links i{font-style:normal;margin:0 10px}
.copy{margin-top:14px;font-size:16px}
</style>
</head>
<body>
<div class="stage">

  <header class="abs topbar">
    <svg class="abs" style="left:118px;top:34px" width="20" height="18"><path d="M0 2h20M0 9h20M0 16h20" stroke="#777" stroke-width="3"/></svg>
    <div class="abs divider" style="left:168px"></div>
    <div class="abs brand"><span class="brand-dot"></span><span class="brand-name">Teamora</span></div>
    <div class="abs user"><span class="avatar" role="img" aria-label="User profile photo"></span>Alex Rowan
      <svg width="14" height="9"><path d="M0 0h14L7 9z" fill="#555"/></svg></div>
    <div class="abs divider" style="left:1076px"></div>
    <svg class="abs" style="left:1103px;top:31px" width="24" height="22"><path d="M0 1h22M0 8h22M0 15h12M0 21h22" stroke="#666" stroke-width="4"/></svg>
    <div class="abs badge" style="left:1116px;top:18px;background:var(--orange)">8</div>
    <div class="abs divider" style="left:1156px"></div>
    <svg class="abs" style="left:1180px;top:30px" width="24" height="24"><circle cx="10" cy="10" r="7.5" fill="none" stroke="#666" stroke-width="3"/><path d="M15.5 15.5l6 6" stroke="#666" stroke-width="3.5" stroke-linecap="round"/></svg>
    <div class="abs divider" style="left:1226px"></div>
    <svg class="abs" style="left:1251px;top:31px" width="22" height="24"><path d="M11 1c5 0 7 4 7 8v6l3 4H1l3-4V9c0-4 2-8 7-8z" fill="#666"/><circle cx="11" cy="21" r="3" fill="#666"/></svg>
    <div class="abs badge" style="left:1258px;top:18px;background:var(--brand)">8</div>
  </header>

  <div class="abs panel">
    <nav class="abs sidebar">
      <div class="side-main">
        <svg width="18" height="16"><rect width="8" height="7" rx="1" fill="#1b8fc4"/><rect x="10" width="8" height="7" rx="1" fill="#1b8fc4"/><rect y="9" width="8" height="7" rx="1" fill="#1b8fc4"/><rect x="10" y="9" width="8" height="7" rx="1" fill="#1b8fc4"/></svg>View Dashboard</div>
      <div class="side-main">
        <svg width="18" height="18"><rect x="1" y="3" width="16" height="14" fill="none" stroke="#1b8fc4" stroke-width="2"/><path d="M1 7h16M5 1v4M13 1v4M5 10h2M9 10h2M13 10h1M5 13h2M9 13h2" stroke="#1b8fc4" stroke-width="2"/></svg>View Event</div>
      <ul class="side-list">
        <li><span>›</span>About Us</li>
        <li><span>›</span>Speakers</li>
        <li><span>›</span>Track</li>
        <li class="active"><span>›</span>Sessions</li>
        <li><span>›</span>Tickets</li>
        <li><span>›</span>Organizers</li>
        <li><span>›</span>Sponsors</li>
        <li><span>›</span>Exhibitor</li>
        <li><span>›</span>Security</li>
        <li><span>›</span>Members</li>
      </ul>
    </nav>
  </div>

  <section class="abs card">
    <div class="card-head">
      <svg width="18" height="18"><circle cx="9" cy="9" r="8" fill="#555"/><path d="M9 9V1A8 8 0 0 1 17 9z" fill="#bbb"/></svg>Session Details</div>
  </section>

  <span class="abs label" style="left:504px;top:278px">Session Name :</span>
  <div class="abs field" style="left:695px;top:265px;width:526px;height:46px">Computer Vision</div>

  <span class="abs label" style="left:504px;top:339px">Session Description :</span>
  <div class="abs field" style="left:695px;top:326px;width:526px;height:104px;align-items:flex-start;padding-top:14px">SURF algorithm</div>

  <span class="abs label" style="left:504px;top:447px">Upload Attachments :</span>
  <svg class="abs" style="left:695px;top:449px" width="20" height="15"><path d="M5 14a5 5 0 0 1-1-10 6 6 0 0 1 11 1 4.5 4.5 0 0 1 0 9z" fill="#1b8fc4"/><path d="M10 12V6M7 9l3-3 3 3" stroke="#fff" stroke-width="2" fill="none"/></svg>
  <div class="abs file" style="left:696px;top:478px">
    <svg width="17" height="19"><path d="M1 1h10l5 5v12H1z" fill="none" stroke="#777" stroke-width="1.4"/><path d="M4 14l4-8 4 8" fill="none" stroke="#777"/></svg>SURF.pdf</div>

  <span class="abs label" style="left:504px;top:528px">Session Location :</span>
  <div class="abs field" style="left:695px;top:515px;width:526px;height:46px"></div>

  <span class="abs label" style="left:504px;top:609px">Session Track :</span>
  <div class="abs field" style="left:695px;top:597px;width:230px;height:45px;padding-left:14px;justify-content:space-between;padding-right:14px">Computer Vision
    <svg width="10" height="6"><path d="M1 1l4 4 4-4" stroke="#555" fill="none" stroke-width="1.4"/></svg></div>

  <span class="abs label" style="left:504px;top:669px">Session Type :</span>
  <div class="abs field" style="left:695px;top:660px;width:524px;height:46px;padding-left:14px;justify-content:space-between;padding-right:10px">Session
    <svg width="26" height="26"><rect width="26" height="26" fill="#1b8fc4"/><path d="M8 11l5 5 5-5" stroke="#fff" fill="none" stroke-width="1.6"/></svg></div>

  <span class="abs label" style="left:509px;top:745px">From Date :</span>
  <div class="abs field" style="left:697px;top:732px;width:206px;height:46px">12 - 10 - 2015</div>

  <span class="abs label" style="left:510px;top:816px">From Time :</span>
  <div class="abs time" style="left:698px;top:804px;background:#fff">
    <div class="hm">10<span>:</span>48</div>
    <div class="spin"><svg width="10" height="6"><path d="M1 5l4-4 4 4" stroke="#555" fill="none"/></svg><svg width="10" height="6"><path d="M1 1l4 4 4-4" stroke="#555" fill="none"/></svg></div>
    <div class="ap">AM</div>
  </div>
  <span class="abs label" style="left:926px;top:816px">To Time :</span>
  <div class="abs time" style="left:1007px;top:804px;background:#fff">
    <div class="hm">10<span>:</span>48</div>
    <div class="spin"><svg width="10" height="6"><path d="M1 5l4-4 4 4" stroke="#555" fill="none"/></svg><svg width="10" height="6"><path d="M1 1l4 4 4-4" stroke="#555" fill="none"/></svg></div>
    <div class="ap">AM</div>
  </div>

  <span class="abs label" style="left:504px;top:886px">Session Speaker :</span>
  <div class="abs field" style="left:695px;top:877px;width:524px;height:46px;padding-left:14px">Select one or more Speaker</div>

  <div class="abs btn">ADD SESSION</div>

  <span class="abs label" style="left:504px;top:1020px">Session List :</span>
  <span class="abs" style="left:506px;top:1053px;font-family:'Open Sans',sans-serif;font-size:12px;color:#444">Computer Vision</span>
  <div class="abs file" style="left:507px;top:1078px">
    <svg width="17" height="19"><path d="M1 1h10l5 5v12H1z" fill="none" stroke="#777" stroke-width="1.4"/><path d="M4 14l4-8 4 8" fill="none" stroke="#777"/></svg>SURF.pdf</div>

  <footer class="abs footer">
    <div class="social"><span></span><span></span><span></span><span></span><span></span></div>
    <div class="foot-links">Home<i>/</i>Contact<i>/</i>Topics<i>/</i>Posts and Comments<i>/</i>Discussion<i>/</i>Videos Links</div>
    <div class="copy">Copyright @ 2015 - 2015.Teamora. All Rights Reserved.</div>
  </footer>

</div>
</body>
</html>
```